Condo Debts Collection Business needs a Web Design (Contest)

I need a site for a client, who works with condo debts collection, and ensure all revenues provided by condo fees will be always available to the building manager of condo on a specific date, regardless of defaults.I have the logo of the companies, and some requirements on layout (kind of slider, menu options, phone number on a noble position, etc).
Updates

Designs look the same

Target Market(s)

I have two targets for this design: - Condominium's building manager. This target is looking for a solution to overdue debts on it's condo. - Residents on condominiums. This target wants to live in a better place, where their neighbors pay their condominium fees on time.

Number of Pages Required

1 page

Requirements
Must have
• - Slider with title, some short text related, a nice image (I prefer happy and/or peaceful family, people doing business, happy friends, and so on).
• - I have a special attention to menu. I'm looking for one I can have a nice effect, more elegant, charming, kind of innovative.
• - Phone number on the top (or clearly visible).
• - Member log in area or icon on the top (or clearly visible).
• - News/articles area.
• - Modern fonts, with good quality, sans-serif on areas where reading is more intensive (prefer Google web-fonts).
• - Colors specified on attached files.
• - Header similar or inspired by the "FILE 3"
Nice to have
• - Clear background color, cause it's better to read larger texts (like articles). Dark backgrounds makes reading difficult.
• - A site with effects (like shadows, lines, gradients, lights) is usually pretty.
• - I pay attention on beautiful footers.
Should not have
• - Images with a lot of money (I don't sell richness, I sell tranquility, peace, harmony, safety).
• - Poor menu.
• - Lots of curves. My customer asked for straight lines.

```html
<!DOCTYPE html>
<html lang="en">
<head>
<meta charset="utf-8">
<title>Serenhold – Condo debts collection business</title>
<link rel="stylesheet" href="https://fonts.googleapis.com/css2?family=Poppins:wght@400;500;600&family=Roboto+Condensed:wght@400;700&family=Open+Sans:wght@400;600&display=swap">
<style>
:root{
  --navy:#1b3a6b;
  --navy-dark:#132c55;
  --orange:#e0641f;
  --ink:#222;
  --muted:#444;
  --mint:#e4fbf6;
  --line:#c9d2de;
}
*{box-sizing:border-box;margin:0;padding:0}
html,body{width:1200px;height:3651px;overflow:hidden}
body{font-family:"Open Sans",sans-serif;color:var(--ink);background:#fff;position:relative}
section,header,footer{position:absolute;left:0;width:1200px}
.abs{position:absolute}
.btn{position:absolute;background:var(--orange);color:#fff;font-family:"Open Sans",sans-serif;display:flex;align-items:center;justify-content:center;border-radius:3px}

/* header */
.site-header{top:0;height:172px;background:#fff;box-shadow:0 2px 8px rgba(0,0,0,.12);z-index:2}
.brand{left:90px;top:70px;display:flex;align-items:center;gap:10px;font-family:"Poppins",sans-serif;font-weight:600;font-size:30px;color:var(--navy)}
.brand-mark{width:22px;height:22px;background:var(--orange)}
.phone{left:795px;top:38px;font-family:"Poppins",sans-serif;font-size:21px;color:#333;display:flex;align-items:center;gap:6px}
.member{left:968px;top:34px;width:142px;height:34px;background:var(--navy);color:#fff;font-family:"Poppins",sans-serif;font-size:15px;display:flex;align-items:center;justify-content:center;border-right:6px solid var(--orange);border-radius:3px}
.nav{top:100px;left:485px;display:flex;gap:0;font-family:"Poppins",sans-serif;font-size:17px;color:#222}
.nav a{position:absolute;white-space:nowrap;text-decoration:none;color:inherit}
.nav a.active{color:var(--navy)}
.search{left:1082px;top:100px}

/* hero */
.hero{top:172px;height:606px;background:linear-gradient(100deg,#dfe7ea 0%,#c9d6d8 35%,#9fae9a 60%,#7d8c6c 100%)}
.hero-photo{position:absolute;inset:0}
.hero h1{position:absolute;left:88px;top:175px;font-family:"Roboto Condensed",sans-serif;font-weight:700;font-size:86px;color:var(--navy);letter-spacing:1px}
.hero p{position:absolute;left:88px;top:270px;font-family:"Roboto Condensed",sans-serif;font-size:38px;color:#1c1c1c}
.hero .btn{left:90px;top:343px;width:162px;height:52px;font-size:22px}
.dots{position:absolute;left:1161px;top:220px;display:flex;flex-direction:column;gap:13px}
.dots span{width:9px;height:9px;border-radius:50%;background:#fff}

/* about */
.about{top:778px;height:507px}
.about-mark{left:140px;top:160px;width:400px;font-family:"Poppins",sans-serif;font-weight:600;font-size:52px;color:var(--navy);display:flex;align-items:center;gap:16px}
.about-mark i{display:block;width:40px;height:40px;background:var(--orange)}
.about .kicker{left:582px;top:104px;font-family:"Poppins",sans-serif;font-size:27px;color:var(--navy)}
.about h2{left:580px;top:135px;font-family:"Poppins",sans-serif;font-weight:500;font-size:46px;color:#111}
.about .copy{left:583px;top:200px;width:500px;font-size:13.5px;line-height:31px;color:#333}
.about .btn{left:583px;top:361px;width:137px;height:36px;font-size:16px}

/* services */
.services{top:1285px;height:640px;background:linear-gradient(90deg,#eef3f7 0%,#fbfcfd 40%,#f5f0ea 70%,#e6ddd2 100%)}
.services h2{left:0;width:1200px;top:100px;text-align:center;font-family:"Poppins",sans-serif;font-weight:400;font-size:46px;color:#111}
.card{position:absolute;top:210px;width:316px;height:328px;background:#fff;border:1px solid #9aa8bd;box-shadow:0 4px 10px rgba(0,0,0,.15);text-align:center}
.card svg{margin-top:42px}
.card h3{font-family:"Poppins",sans-serif;font-weight:500;font-size:23px;margin-top:14px;color:#111}
.card p{font-size:13.5px;line-height:26px;color:#333;padding:8px 26px 0}
.card.featured{background:var(--navy);border-color:var(--navy)}
.card.featured h3,.card.featured p{color:#fff}

/* debts */
.debts{top:1925px;height:650px}
.debts .frame{left:83px;top:155px;width:612px;height:375px;border:2px solid var(--navy)}
.debts h2{left:121px;top:203px;font-family:"Poppins",sans-serif;font-weight:500;font-size:34px;color:#111}
.debts .copy{left:121px;top:262px;width:460px;font-size:14px;line-height:29px;color:#333}
.debts .btn{left:120px;top:455px;width:112px;height:29px;font-size:14px;border-radius:2px}
.debts .media{left:595px;top:172px;width:512px;height:338px;background:linear-gradient(135deg,#d9dcdf,#b9bec4 50%,#8f969e);border:1px solid #aab}
.play{left:816px;top:310px}

/* news */
.news{top:2575px;height:655px;background:var(--mint)}
.news h2{left:0;width:1200px;top:78px;text-align:center;font-family:"Poppins",sans-serif;font-weight:400;font-size:46px;color:#111}
.post{position:absolute;top:195px;width:336px}
.post .thumb{height:202px}
.post .body{position:absolute;left:24px;top:168px;width:288px;height:185px;background:#fff;box-shadow:0 3px 10px rgba(0,0,0,.15);text-align:center}
.post time{display:block;font-size:14px;color:#333;margin-top:16px}
.post h3{font-family:"Poppins",sans-serif;font-weight:500;font-size:17px;margin-top:12px;color:#111}
.post p{font-size:12.5px;line-height:21px;color:#444;margin-top:6px;padding:0 20px}
.post .btn{left:82px;top:140px;width:124px;height:28px;font-size:14px;border-radius:2px}

/* footer */
.site-footer{top:3230px;height:421px;background:linear-gradient(180deg,#ffffff 0%,#f4f5f4 45%,#b9c2b2 75%,#6f7d63 100%)}
.footer-brand{left:0;width:1200px;top:125px;justify-content:center;display:flex;align-items:center;gap:10px;font-family:"Poppins",sans-serif;font-weight:600;font-size:28px;color:var(--navy)}
.footer-brand i{width:20px;height:20px;background:var(--orange);display:block}
.footer-nav{left:0;width:1200px;top:204px;display:flex;justify-content:center;gap:46px;font-family:"Poppins",sans-serif;font-size:17px;color:#222}
.social{left:0;width:1200px;top:258px;display:flex;justify-content:center;gap:9px}
.social span{width:44px;height:44px;border:2px solid #222;border-radius:50%;display:block}
.copyright{left:0;width:1200px;top:333px;text-align:center;font-size:13px;color:#222}
</style>
</head>
<body>

<header class="site-header">
  <div class="abs brand"><i class="brand-mark"></i>SERENHOLD</div>
  <div class="abs phone">
    <svg width="16" height="16" viewBox="0 0 24 24"><path fill="#e0641f" d="M6.6 10.8a15.1 15.1 0 0 0 6.6 6.6l2.2-2.2c.3-.3.7-.4 1-.2 1.1.4 2.3.6 3.6.6.6 0 1 .4 1 1V20c0 .6-.4 1-1 1A17 17 0 0 1 3 4c0-.6.4-1 1-1h3.5c.6 0 1 .4 1 1 0 1.3.2 2.5.6 3.6.1.3 0 .7-.2 1z"/></svg>
    0800 555 0199
  </div>
  <div class="abs member">Member login</div>
  <nav class="nav abs">
    <a class="active" style="left:0">Home</a>
    <a style="left:105px">About us</a>
    <a style="left:238px">Services</a>
    <a style="left:368px">News</a>
    <a style="left:468px">Contact Us</a>
  </nav>
  <svg class="abs search" width="26" height="26" viewBox="0 0 24 24"><circle cx="10" cy="10" r="6.5" fill="none" stroke="#111" stroke-width="2.6"/><line x1="15" y1="15" x2="21" y2="21" stroke="#111" stroke-width="2.8" stroke-linecap="round"/></svg>
</header>

<section class="hero">
  <div class="hero-photo" role="img" aria-label="Happy family walking together along a green coastal hillside"></div>
  <h1>SERENHOLD</h1>
  <p>Condo debts collection business</p>
  <div class="btn">View More</div>
  <div class="dots"><span></span><span></span><span></span><span></span></div>
</section>

<section class="about">
  <div class="abs about-mark"><i></i>SERENHOLD</div>
  <div class="abs kicker">About</div>
  <h2 class="abs">Serenhold</h2>
  <p class="abs copy">The point of using Lorem Ipsum is that it has a more-or-less normal distribution of letters, as opposed to using 'Content here, content here', making it look like readable English. Many desktop publishing packages and web page editors now use Lorem Ipsum as their default model text, and a search for 'lorem ipsum' will uncover many web sites still in their infancy.</p>
  <div class="btn">Read More</div>
</section>

<section class="services" role="region" aria-label="Our services">
  <h2 class="abs">Our Services</h2>
  <div class="card" style="left:94px">
    <svg width="110" height="110" viewBox="0 0 110 110" fill="none" stroke="#1b3a6b" stroke-width="3"><circle cx="55" cy="32" r="16"/><path d="M48 50h14M50 56h10"/><path d="M55 8v6M31 32h-6M85 32h-6M38 15l4 4M72 15l-4 4"/><path d="M20 60v30l15 12M90 60v30l-15 12M20 60l14 18M90 60l-14 18"/></svg>
    <h3>Neque quisquam</h3>
    <p>The point of using Lorem Ipsum is that it has a more-or-less normal distribution of letters, as opposed to using</p>
  </div>
  <div class="card featured" style="left:448px">
    <svg width="110" height="110" viewBox="0 0 110 110" fill="none" stroke="#fff" stroke-width="3"><rect x="30" y="12" width="50" height="34"/><path d="M40 24h30M40 33h20"/><rect x="18" y="52" width="74" height="8"/><circle cx="28" cy="72" r="8"/><circle cx="82" cy="72" r="8"/><path d="M14 100v-10h28v10M68 100v-10h28v10M55 60v40"/></svg>
    <h3>dolorem ipsum quia</h3>
    <p>The point of using Lorem Ipsum is that it has a more-or-less normal distribution of letters, as opposed to using</p>
  </div>
  <div class="card" style="left:792px">
    <svg width="110" height="110" viewBox="0 0 110 110" fill="none" stroke="#1b3a6b" stroke-width="3"><circle cx="55" cy="24" r="14"/><rect x="18" y="36" width="74" height="48"/><circle cx="38" cy="58" r="10"/><path d="M56 50h26M56 60h26M56 70h18"/><path d="M45 96h20M55 84v12"/></svg>
    <h3>porro quisquam</h3>
    <p>The point of using Lorem Ipsum is that it has a more-or-less normal distribution of letters, as opposed to using</p>
  </div>
</section>

<section class="debts">
  <div class="abs frame"></div>
  <div class="abs media" role="img" aria-label="Business team meeting around a table, seen from above"></div>
  <svg class="abs play" width="70" height="70" viewBox="0 0 70 70"><circle cx="35" cy="35" r="33" fill="rgba(255,255,255,.55)"/><path d="M28 22l20 13-20 13z" fill="#fff"/></svg>
  <h2 class="abs">Debts Collection</h2>
  <p class="abs copy">It is a long established fact that a reader will be distracted by the readable content of a page when looking at its layout. The point of using Lorem Ipsum is that it has a more-or-less normal distribution of letters, as opposed to using 'Content here, content here', making it look like readable English. Many desktop publishing packages and web page editors now use Lorem Ipsum as their default</p>
  <div class="btn">Learn More</div>
</section>

<section class="news">
  <h2 class="abs">Latest News</h2>
  <article class="post" style="left:68px">
    <div class="thumb" role="img" aria-label="Couple running on a beach under a blue sky" style="background:linear-gradient(180deg,#7fb1d8,#c9dbe6 60%,#d9c7a7)"></div>
    <div class="body">
      <time>JAN 25,2019</time>
      <h3>Dolorem ipsum quia dolor</h3>
      <p>It has survived not only five centuries, but also the leap into electronic</p>
      <div class="btn">Read More</div>
    </div>
  </article>
  <article class="post" style="left:430px">
    <div class="thumb" role="img" aria-label="Hands working with a calculator and papers on a desk" style="background:linear-gradient(135deg,#3b4a5e,#a8b3bf 55%,#e3e0d8)"></div>
    <div class="body">
      <time>JAN 25,2019</time>
      <h3>Dolorem ipsum quia dolor</h3>
      <p>It has survived not only five centuries, but also the leap into electronic</p>
      <div class="btn">Read More</div>
    </div>
  </article>
  <article class="post" style="left:797px">
    <div class="thumb" role="img" aria-label="Friends walking on a ship deck by the sea" style="background:linear-gradient(180deg,#6f9cc4,#c8d8e4 55%,#8894a2)"></div>
    <div class="body">
      <time>JAN 25,2019</time>
      <h3>Dolorem ipsum quia dolor</h3>
      <p>It has survived not only five centuries, but also the leap into electronic</p>
      <div class="btn">Read More</div>
    </div>
  </article>
</section>

<footer class="site-footer" role="contentinfo">
  <div class="abs footer-brand"><i></i>SERENHOLD</div>
  <nav class="abs footer-nav"><span>Home</span><span>About</span><span>Service</span><span>News</span><span>Contact us</span></nav>
  <div class="abs social" aria-label="Social links"><span></span><span></span><span></span><span></span><span></span></div>
  <p class="abs copyright">Copyright © 2019 All Rights Reserved</p>
</footer>

</body>
</html>
```